Business Card Design for BrightvaleMedia.com

--I need a business card design for my company BrightvaleMedia.com

I have attached my logo...I want the brightvale media logo on the front of the business card, and then I want The Quillstone Chief on the back of it with my information.

I would like to see a light colored background as well as a dark colored background

FRONT:
BRIGHTVALE MEDIA LOGO
248 N. Larkmoor
3rd Floor
San Diego CA 92173
www.BrightvaleMedia.com

Advanced Website & App Development
Websites, Apps, Online Voucher Systems

Leading Edge Marketing Services
SMS, VB, SMM, SEM,

BACK:
QUILLSTONE CHIEF LOGO
Dorian Pelletta
The Quillstone Chief
Call Or Text: 619-555-0148
Dorian@QuillstoneChief.example
www.QuillstoneChief.example

Target Market(s)

small business owners

Industry/Entity Type

Business Consultant

Contact Information for Business Card

FRONT:
BRIGHTVALE MEDIA LOGO
248 N. Larkmoor
3rd Floor
San Diego CA 92173
www.BrightvaleMedia.com

SMS, VB, SMM, SEM,

BACK:
QUILLSTONE CHIEF LOGO
Dorian Pelletta
The Quillstone Chief
Dorian@QuillstoneChief.example
www.QuillstoneChief.example

Requirements
Must have
• add this quote on it somewhere, anywhere,preferrably on back
• "The Fastest Way To Success Is To Take Action”
• — Dorian Pelletta, Quillstone Chief
Nice to have
• open
Should not have
• red

```html
<!DOCTYPE html>
<html lang="en">
<head>
<meta charset="utf-8">
<title>Brightvale Media – Business Card</title>
<link rel="stylesheet" href="https://fonts.googleapis.com/css2?family=Source+Sans+3:wght@400;600;700&display=swap">
<style>
  :root {
    --backdrop-top: #2a2a2a;
    --backdrop-bottom: #050505;
    --card-light: #f3f3f3;
    --card-dark: #0a6ea8;
    --brand-blue: #1a6aa3;
    --ink: #2b2b2b;
    --white: #ffffff;
  }
  * { margin: 0; padding: 0; box-sizing: border-box; }
  html, body { width: 1200px; height: 900px; overflow: hidden; }
  body {
    position: relative;
    background: linear-gradient(180deg, var(--backdrop-top) 0%, #1a1a1a 55%, var(--backdrop-bottom) 100%);
    font-family: "Source Sans 3", "Myriad Pro", Arial, sans-serif;
  }
  .card {
    position: absolute;
    top: 184px;
    height: 490px;
    border-radius: 12px;
    text-align: center;
    box-shadow: 0 2px 6px rgba(0,0,0,0.35);
  }
  .card--back { left: 299px; width: 301px; background: var(--card-light); color: var(--ink); }
  .card--front { left: 645px; width: 305px; background: var(--card-dark); color: var(--white); }

  .wordmark {
    position: absolute;
    left: 0; right: 0;
    font-weight: 600;
    letter-spacing: 1.5px;
    white-space: nowrap;
  }
  .card--back .wordmark { top: 134px; font-size: 25px; color: var(--brand-blue); }
  .card--front .wordmark { top: 134px; font-size: 26px; color: var(--white); }

  .block { position: absolute; left: 0; right: 0; font-size: 14px; line-height: 18px; }

  .person { top: 237px; }
  .person__name { font-size: 17px; font-weight: 700; color: var(--brand-blue); line-height: 20px; }
  .person__title { font-size: 14px; }
  .contact { top: 306px; }

  .address { top: 244px; }
  .services-dev { top: 311px; }
  .services-mkt { top: 357px; }
  .website { top: 418px; }
</style>
</head>
<body>
  <section class="card card--back" aria-label="Card back">
    <div class="wordmark">QUILLSTONE CHIEF</div>
    <div class="block person">
      <p class="person__name">Dorian Pelletta</p>
      <p class="person__title">The Quillstone Chief</p>
    </div>
    <div class="block contact">
      <p>619-555-0148</p>
      <p>Dorian@QuillstoneChief.example</p>
      <p>www.QuillstoneChief.example</p>
    </div>
  </section>

  <section class="card card--front" aria-label="Card front">
    <div class="wordmark">BRIGHTVALE MEDIA</div>
    <div class="block address">
      <p>248 N. Larkmoor</p>
      <p>3rd Floor, San Diego CA 92173</p>
    </div>
    <div class="block services-dev">
      <p>Advanced Website &amp; App Development</p>
      <p>Websites | Apps | Online Voucher Systems</p>
    </div>
    <div class="block services-mkt">
      <p>Leading Edge Marketing Services</p>
      <p>SMS | VB | SMM | SEM,</p>
    </div>
    <div class="block website">
      <p>www.BrightvaleMedia.com</p>
    </div>
  </section>
</body>
</html>
```